Clear Plastic Card Design

I am looking to have a business card designed from my logo icon. I am looking to match the style of a different business card I have attached in the files.
Looking for a card that is plastic, with layers of transparency in the shape of my logo icon (also attached in the files) - not a circle like the other card. The winning design will incorporate the red icon logo on the front and back and include the charity's name, "Light for the Weary Souls" in the same or similar font, as well as an email and phone number. For now, use the email: email@lightfortheweary-mail.org and the phone number 555-382-7194.
We like how the sample business card has transparency, partial and full opacity layers and a matching color scheme. Files will need to be in vector so that our business card printing company can work with it.
UPDATE:
We've some excellent designs in, thank you everyone! I got an early review from the owner, and he requested a minor redirect to find his perfect design. He wants the design to stand out by NOT being a rectangle. Try instead a circle, square, or best yet - something that falls in the outline of the logo icon, either fully or partially. Thank you, everyone!
Light for the Weary Souls text should be incorporated as well as a phone and email.

```html
<!DOCTYPE html>
<html lang="en">
<head>
<meta charset="utf-8">
<title>Light for the Weary Souls – Business Card</title>
<link href="https://fonts.googleapis.com/css2?family=Poppins:ital,wght@0,500;0,700;1,400&display=swap" rel="stylesheet">
<style>
  :root {
    --page-bg: #e9e5e3;
    --card-frost: rgba(255, 255, 255, 0.9);
    --brand-red: #c4101c;
    --brand-orange: #e8410f;
    --ink-dark: #3b3838;
    --ink-soft: #2f2d2d;
    --on-brand: #ffffff;
  }
  html, body {
    margin: 0;
    padding: 0;
    width: 1200px;
    height: 900px;
    overflow: hidden;
    background: var(--page-bg);
  }
  .canvas {
    position: relative;
    width: 1200px;
    height: 900px;
    font-family: "Poppins", sans-serif;
  }
  .business-card {
    position: absolute;
    left: 110px;
    top: 147px;
    width: 678px;
    height: 606px;
  }
  .card-body {
    position: absolute;
    inset: 0;
    background: var(--card-frost);
    box-shadow: 0 2px 10px rgba(0, 0, 0, 0.08);
  }
  .charity-name {
    position: absolute;
    left: 44px;
    top: 58px;
    margin: 0;
    font-weight: 700;
    font-size: 50px;
    line-height: 61px;
    color: var(--brand-red);
    text-transform: uppercase;
  }
  .contact-phone {
    position: absolute;
    left: 42px;
    top: 392px;
    display: flex;
    align-items: center;
    gap: 16px;
    font-weight: 500;
    font-size: 44px;
    line-height: 52px;
    letter-spacing: 2px;
    color: var(--ink-dark);
  }
  .phone-icon {
    width: 52px;
    height: 52px;
    display: block;
  }
  .contact-email {
    position: absolute;
    left: 44px;
    top: 472px;
    font-style: italic;
    font-weight: 400;
    font-size: 25px;
    color: var(--ink-soft);
  }
  .brand-block {
    position: absolute;
    left: 430px;
    top: 50px;
    width: 330px;
    height: 330px;
    background: var(--brand-orange);
    display: flex;
    align-items: center;
    justify-content: center;
  }
  .brand-name {
    margin: 0;
    font-weight: 700;
    font-size: 32px;
    line-height: 42px;
    text-align: center;
    color: var(--on-brand);
    text-transform: uppercase;
  }
</style>
</head>
<body>
  <main class="canvas">
    <section class="business-card">
      <div class="card-body"></div>

      <h1 class="charity-name">Light for<br>the Weary<br>Souls</h1>

      <div class="brand-block">
        <p class="brand-name">Light for the<br>Weary Souls</p>
      </div>

      <div class="contact-phone">
        <svg class="phone-icon" viewBox="0 0 58 58" aria-hidden="true">
          <circle cx="29" cy="29" r="29" fill="#d3161b"/>
          <path d="M21 17c1.5-1 3-.6 3.8.8l2.4 4.3c.7 1.3.3 2.7-.8 3.5l-1.6 1.1c1.2 2.9 3.5 5.4 6.3 6.9l1.2-1.5c.9-1.1 2.4-1.4 3.6-.6l4.1 2.7c1.3.9 1.6 2.5.6 3.8l-1.6 2c-1.4 1.7-3.8 2.3-5.9 1.4C25.5 38.7 19.4 32.3 16.7 24.6c-.7-2.1 0-4.4 1.8-5.7z" fill="#ffffff"/>
          <path d="M32 15a11 11 0 0 1 11 11M32 20a6 6 0 0 1 6 6" stroke="#ffffff" stroke-width="2.2" fill="none" stroke-linecap="round"/>
        </svg>
        <span>555-382-7194</span>
      </div>

      <div class="contact-email">email@lightfortheweary-mail.org</div>
    </section>
  </main>
</body>
</html>
```